Coastal Learner Bureau business cards

Australian company about to start offering its services. We recruit international students to come to study English, vocational education and postgraduate courses in Australia. We help them find the institution and select the right city they want to come to Australia. We are a young, online oriented and supportive agency. Our clients are between 18 and 35 years old, mainly University students, young professionals or people with work experience. We provide much more information that any other agency offer. We administrate a Facebook group with more than 11.000 members that daily ask questions about general information when coming to Australia, while they are here and even after they leave the country

Target Market(s)

International students from South America, Central America and Europe

Industry/Entity Type

Student

Contact Information for Business Card

Tomas Bilbrea
Managing Director
tomas@kelvarin.com.au
www.kelvoria.com.au
+61 491058264
Melbourne, Australia

Font styles to use
Serif
Sans Serif

Colors

Designer to choose colors to be used in the design.

Requirements
Must have
• Horizontal design
• Standard business card size and shape. If font uses green or yellow colours, they will have to match the ones from the logo
Nice to have
• UPDATE: Use the contents of the green image to design one of the card sides. Use our logo in the background of that side as watermark.
• Passport image, or immigration stamps. A picture of the Yarra River (from Melbourne) would be cool as well.
Should not have
• Non-standard business card size and shape
• Not black as the background colour of any sides as we are not a VIP agency or a hight class service. We are orientes to young people and they like colours, pictures, something attractive.
• Vertical design
• NO YELLOW or BLACK AS THE BACKGROUND COLOUR OF ANY SIDE OF THE BIZ CARD

```html
<!DOCTYPE html>
<html lang="en">
<head>
<meta charset="utf-8">
<title>Coastal Learner Bureau – Business Cards</title>
<link href="https://fonts.googleapis.com/css2?family=Roboto:wght@400;500&family=Roboto+Condensed:wght@700&display=swap" rel="stylesheet">
<style>
  :root {
    --brand-green: #13603e;
    --brand-green-light: #1c7049;
    --brand-yellow: #e2b916;
    --paper-white: #fbfbfa;
    --backdrop: #e6e6e4;
    --text-light: #ffffff;
  }
  * { margin: 0; padding: 0; box-sizing: border-box; }
  html, body {
    width: 1200px; height: 886px; overflow: hidden;
    background: var(--backdrop);
    font-family: "Roboto", Arial, sans-serif;
  }
  .sheet {
    width: 1200px; height: 886px;
    display: flex; flex-direction: column;
    align-items: center; justify-content: center; gap: 40px;
  }
  .card {
    position: relative;
    width: 620px; height: 354px;
    overflow: hidden;
    box-shadow: 0 6px 18px rgba(0,0,0,0.18);
  }
  .card--back {
    background: linear-gradient(135deg, var(--brand-green-light), var(--brand-green));
    display: flex; align-items: center; justify-content: center;
  }
  .brand-name {
    font-family: "Roboto", Arial, sans-serif;
    font-weight: 500;
    font-size: 34px;
    line-height: 1.1;
    white-space: nowrap;
    display: flex; align-items: center; gap: 14px;
  }
  .brand-name__dot { width: 16px; height: 16px; border-radius: 50%; background: currentColor; flex: none; }
  .card--back .brand-name { color: var(--text-light); }
  .card--front { background: var(--brand-green); }
  .card__shapes { position: absolute; inset: 0; width: 620px; height: 354px; }
  .card--front .brand-name {
    position: absolute; left: 28px; top: 160px; width: 320px;
    color: var(--brand-green); font-size: 23px; gap: 10px; justify-content: center;
  }
  .card--front .brand-name__dot { width: 12px; height: 12px; }
  .contact {
    position: absolute; left: 405px; top: 96px;
    color: var(--text-light);
  }
  .contact__name {
    font-family: "Roboto Condensed", "Arial Narrow", sans-serif;
    font-weight: 700; font-size: 26px; letter-spacing: 0.3px;
    color: var(--brand-yellow); text-transform: uppercase; line-height: 1;
  }
  .contact__role { font-size: 15px; font-weight: 500; margin-top: 4px; }
  .contact__place { font-size: 14px; margin-top: 14px; }
  .contact__lines { list-style: none; margin-top: 14px; font-size: 14px; line-height: 1.55; white-space: nowrap; }
  .contact__label { color: var(--brand-yellow); font-weight: 500; margin-right: 4px; }
</style>
</head>
<body>
<main class="sheet">
  <section class="card card--back" aria-label="Card back">
    <p class="brand-name"><span class="brand-name__dot"></span>Coastal Learner Bureau</p>
  </section>

  <section class="card card--front" aria-label="Card front">
    <svg class="card__shapes" viewBox="0 0 620 354" aria-hidden="true">
      <defs>
        <linearGradient id="greenSheen" x1="0" y1="1" x2="1" y2="0">
          <stop offset="0" stop-color="#1c7049"/>
          <stop offset="1" stop-color="#13603e"/>
        </linearGradient>
      </defs>
      <rect width="620" height="354" fill="url(#greenSheen)"/>
      <path d="M0 0 H364 C420 95 410 250 268 354 H0 Z" fill="var(--brand-yellow)"/>
      <path d="M0 0 H356 C406 95 396 250 250 354 H0 Z" fill="var(--brand-green)"/>
      <path d="M0 0 H350 C398 95 388 250 240 354 H0 Z" fill="var(--paper-white)"/>
    </svg>
    <p class="brand-name"><span class="brand-name__dot"></span>Coastal Learner Bureau</p>
    <div class="contact">
      <h1 class="contact__name">Tomas Bilbrea</h1>
      <p class="contact__role">Managing Director</p>
      <p class="contact__place">Melbourne, Australia</p>
      <ul class="contact__lines">
        <li><span class="contact__label">P:</span>+61 491058264</li>
        <li><span class="contact__label">E:</span>tomas@kelvarin.com.au</li>
        <li><span class="contact__label">W:</span>www.kelvoria.com.au</li>
      </ul>
    </div>
  </section>
</main>
</body>
</html>
```